Velmisa Sunscreen and Tanning Lotion Flyer

I need a flyer to post to pm Chatterloop and other social media.
It most have these components:
Modern, sensational fonts, Original Art work, Sexy, Theme based on Verses
Women, bikini, tan, attractive
Ocean scenes, Palm Trees (same green as bottle)
VELMISA Logo (Slight shading background)
Quote “Quality by Design”
Bright, Sunny, fun
Save in PDF, GIF, and EPS

Reason: I have some designer who have not completed their work. Thank you.

Target Market(s)

Sunscreen tanning lotion

Industry/Entity Type

Media

Colors
9bcb3c

Requirements
Must have
• Modern, sensational fonts, Original Art work, Sexy, Theme based on Verses
• Women, bikini, tan, attractive
• Ocean scenes, Palm Trees (same green as bottle)
• VELMISA Logo (Slight shading in the background)
• Quote “Quality by Design”
• Bright, Sunny, fun
• Save in PDF, GIF, and EPS
Nice to have
• flyer designed with these verses in mind.
• •When the warm sea breeze exhales its sweet serenity, and the frothy sea cloaks your body in indulgence, the rays of the sun completes the objective.
• • The water splatters against the shore, and the blue stillness showers me tranquility and perfection and I find myself covered by the seas delightful symphony.
• •The sea breeze feels like a long lost friend, as it delightfully caresses your sweaty skin. And like that long lost friend, you embrace, take a deep breath, and relish the gusto of life.
• • The stunningly-turquoise sea beckons and we enthusiastically surrender to its allure. A smile from the white puffy clouds above. A soothing massage from the wet, cool sand below our feet, bliss in the sun.
• •Seagulls have white plumage, not unlike the color to the clouds overhead. Their hue is undistinguishable from the whitecaps spawned by waves on a blustery day. Mother Nature must be an artist whose philosophy is harmony in symmetry
• It would be nice to have these verses incorporated in the Flyer, but it is not necessary.
Should not have
• Must not have someone else's work, all graphic need to be original.

```html
<!DOCTYPE html>
<html lang="en">
<head>
<meta charset="utf-8">
<title>Velmisa Sunscreen &amp; Suntan Lotion Flyer</title>
<link rel="stylesheet" href="https://fonts.googleapis.com/css2?family=Exo+2:wght@700;800&family=Cabin:wght@600;700&family=Cormorant+Garamond:wght@500&family=Open+Sans:ital,wght@0,600;0,700;0,800;1,600&family=Great+Vibes&family=Cinzel:wght@600&family=Rubik+Dirt&display=swap">
<style>
  :root {
    --page: #ffffff;
    --sand: #e7dccb;
    --bronze: #a97b3c;
    --bronze-dark: #8a5f27;
    --ink: #0d0d0d;
    --lime: #b4f21e;
    --lime-light: #d2ff2a;
    --leaf: #1f8a2a;
    --cream: #fff3dc;
    --gold: #d9a94a;
    --text-dark: #1a1a1a;
    --white: #ffffff;
  }
  * { margin: 0; padding: 0; box-sizing: border-box; }
  html, body { width: 788px; height: 1200px; overflow: hidden; background: var(--page); }
  .flyer { position: relative; width: 788px; height: 1200px; overflow: hidden; }
  .flyer__shapes { position: absolute; inset: 0; }

  .tagline {
    position: absolute; right: 54px; top: 44px;
    font-family: "Exo 2", sans-serif; font-weight: 800;
    font-size: 30px; line-height: 34px; text-align: right;
    color: var(--white); text-shadow: 1px 2px 2px rgba(0,0,0,.35);
  }
  .spf {
    position: absolute; right: 54px; top: 138px; text-align: right;
    font-family: "Exo 2", sans-serif; color: var(--white);
  }
  .spf__value { font-size: 34px; font-weight: 800; letter-spacing: -1px; }
  .spf__unit { font-size: 20px; font-weight: 800; }
  .spf__volume { display: block; font-family: "Open Sans", sans-serif; font-size: 10px; font-weight: 700; margin-top: -4px; }

  .uv-badge {
    position: absolute; left: 76px; top: 484px; width: 224px; height: 224px;
    border-radius: 50%;
    background: radial-gradient(circle at 45% 30%, #e49a3a 0%, #c96f12 55%, #8e4a08 100%);
    border: 2px solid #f3d9b0;
    box-shadow: 0 4px 10px rgba(0,0,0,.4);
    display: flex; align-items: center; justify-content: center; text-align: center;
    font-family: "Cabin", sans-serif; font-weight: 700;
    font-size: 31px; line-height: 38px; color: var(--cream);
    text-shadow: 1px 2px 2px rgba(0,0,0,.45);
  }

  .description {
    position: absolute; right: 40px; top: 350px; text-align: right;
    font-family: "Cormorant Garamond", serif; font-weight: 500;
    font-size: 14.6px; line-height: 22.8px; color: var(--text-dark);
  }

  .origin {
    position: absolute; left: 406px; top: 818px; width: 332px;
    font-family: "Open Sans", sans-serif; font-weight: 600; font-size: 17.5px;
    color: var(--text-dark); border-bottom: 1.5px solid var(--text-dark); padding-bottom: 2px;
  }
  .contact-note {
    position: absolute; left: 406px; top: 850px;
    font-family: "Open Sans", sans-serif; font-style: italic; font-weight: 600;
    font-size: 14.5px; color: var(--text-dark);
  }
  .contact-email {
    position: absolute; right: 40px; top: 878px;
    font-family: "Open Sans", sans-serif; font-weight: 800;
    font-size: 25px; letter-spacing: 1.5px; color: var(--text-dark);
  }

  .slogan {
    position: absolute; right: 52px; top: 952px; text-align: right;
    font-family: "Great Vibes", cursive; font-size: 52px; line-height: 66px;
    color: var(--white); text-shadow: 2px 3px 3px rgba(0,0,0,.55);
  }

  .new-flag {
    position: absolute; left: 48px; top: 770px;
    font-family: "Rubik Dirt", sans-serif; font-size: 88px; line-height: 1;
    color: var(--lime-light); transform: rotate(-14deg); transform-origin: left bottom;
    letter-spacing: 2px;
  }

  .brand { position: absolute; left: 58px; top: 884px; width: 360px; text-align: center; }
  .brand__mark {
    width: 148px; height: 148px; margin: 0 auto 14px; border-radius: 50%;
    background: var(--gold);
  }
  .brand__name {
    font-family: "Cinzel", serif; font-weight: 600; font-size: 76px; line-height: 80px;
    color: var(--gold); letter-spacing: 1px;
  }
  .brand__name sup { font-size: 26px; vertical-align: 40px; }
  .brand__tagline {
    font-family: "Cabin", sans-serif; font-weight: 600; font-size: 22px;
    color: var(--gold); margin-top: 2px; letter-spacing: .3px;
  }
</style>
</head>
<body>
<main class="flyer">
  <svg class="flyer__shapes" width="788" height="1200" viewBox="0 0 788 1200">
    <defs>
      <linearGradient id="beachTone" x1="0" y1="0" x2="1" y2="1">
        <stop offset="0" stop-color="#7fb24a"/>
        <stop offset="0.25" stop-color="#e9e4da"/>
        <stop offset="0.55" stop-color="#c98d5a"/>
        <stop offset="1" stop-color="#e3d6c2"/>
      </linearGradient>
      <linearGradient id="limePanel" x1="0" y1="0" x2="1" y2="1">
        <stop offset="0" stop-color="#a9ec18"/>
        <stop offset="1" stop-color="#c8fb12"/>
      </linearGradient>
      <filter id="cardShadow" x="-5%" y="-5%" width="110%" height="110%">
        <feDropShadow dx="0" dy="2" stdDeviation="3" flood-opacity=".35"/>
      </filter>
    </defs>
    <rect class="card" x="20" y="20" width="748" height="1164" fill="var(--sand)" filter="url(#cardShadow)"/>
    <polygon class="beach-photo" role="img" aria-label="Photo: tanned woman in a black swimsuit and wide sun hat sitting on white beach sand under palm fronds"
      points="20,20 504,20 712,284 276,756 20,456" fill="url(#beachTone)"/>
    <polygon class="corner-band" points="504,20 768,20 768,344" fill="var(--bronze)"/>
    <polygon class="divider-band" points="20,452 276,744 716,276 768,328 768,1184 20,1184" fill="var(--bronze)"/>
    <polygon class="dark-panel" points="20,468 272,760 590,1184 20,1184" fill="var(--ink)"/>
    <line class="leaf-rule" x1="281" y1="752" x2="713" y2="290" stroke="var(--leaf)" stroke-width="5"/>
    <polygon class="lime-panel" points="290,758 716,298 768,350 768,1184 606,1184" fill="url(#limePanel)"/>
  </svg>

  <div class="tagline">Quality by<br>Design</div>
  <div class="spf"><span class="spf__value">50</span><span class="spf__unit">SPF</span><span class="spf__volume">8FL OZI 237ml</span></div>

  <div class="uv-badge">Reduction<br>to (UVA)<br>and (UVB)<br>Radiation</div>

  <p class="description">
    Velmisa<br>
    Tanning Lotion is<br>
    the most extra<br>
    ordinary and innovative<br>
    sun tanning product to<br>
    emerge in several generations.<br>
    The constituents of this product are<br>
    formidable substances that protect the<br>
    skin against the aftermath of sun<br>
    exposure-before you exposed yourself to the sun's<br>
    rays. The Aloe Vera in this product along with other<br>
    oils and cream are specifically manufactured to lessen<br>
    the symptoms of extended exposurre to the sun. Velmisa is<br>
    designed to provide a broad spectrum protection (50) that assist<br>
    in the reduction of (UVA) and (UVB) radiation to create a<br>
    magnificent sun absorbing and long lasting deep dark bronzing<br>
    experience. It is an elegant gift from nature that leaves your skin feeling<br>
    fresh and not greasy. It is water resistant contains no preservatives or coloring<br>
    agents. Velmisa Tanning Lotion is manufactured utilizing the finest raw materials.
  </p>

  <div class="origin">Product of the USA: Coral Bay, NY</div>
  <div class="contact-note">For comments or suggestions please contact us at</div>
  <div class="contact-email">velmisa87@sunmail.com</div>

  <div class="slogan">Sophisticated<br>Velvety<br>Smooth</div>

  <div class="new-flag">NEW</div>

  <div class="brand">
    <div class="brand__mark"></div>
    <div class="brand__name">VELMISA<sup>™</sup></div>
    <div class="brand__tagline">SUNSCREEN &amp; SUNTAN LOTION</div>
  </div>
</main>
</body>
</html>
```